Fahrzeugbeschriftung für Hersteller von Campingzubehör
Perfekt! Genau das was wir uns vorgestellt haben. Vielen Dank
Zielgruppe
Wir sind Hersteller von Campingzubehör, made in Germany! Angesprochen werden sollen, Camper, Händler und Vermieter von Freizeitfahrzeugen. Hier soll ein Sonnensegel kreiert werden, als Werbemaßnahme für die o.g. Zielgruppe. Dieses Sonnensegel soll auf die Einzigartigkeit des Campers wieder spiegeln. Für den schönsten Schatten der Welt!
Campen ist IN! und Individualität wird groß geschrieben. Das Alter der Zielgruppe reicht von 42-80 und legt Wert auf Nachhaltigkeit, Qualität, schätzt den Komfort, aber eben auch das Hobby und die damit verbundene Reiselust.
Aufgabenstellung
Druckformat ist eines 3m breit und 2,2m hoch und 1m breit und 2,2m hoch, Druckvorlage ist dabei. Wichtig ist die HP
www.zeltholmgear.com
Das Banner soll dann aussehen wie dies auf der erste Seite des Flyers

```html
<!DOCTYPE html>
<html lang="de">
<head>
<meta charset="utf-8">
<title>Zeltholm Gear – Individuell bedruckbare Sunblocker</title>
<link rel="stylesheet" href="https://fonts.googleapis.com/css2?family=Source+Sans+3:wght@400;600;700&display=swap">
<style>
  :root {
    --grass-dark: #4f7a1f;
    --grass-mid: #6fa524;
    --grass-bright: #9fd02a;
    --brand-green: #a0c553;
    --accent-yellow: #f2ea12;
    --ink: #161616;
    --paper: #ffffff;
  }
  html, body {
    margin: 0;
    padding: 0;
    width: 1200px;
    height: 880px;
    overflow: hidden;
    background: var(--paper);
  }
  .flyer {
    position: relative;
    width: 1200px;
    height: 880px;
    overflow: hidden;
    font-family: "Source Sans 3", sans-serif;
  }
  .scene-photo {
    position: absolute;
    inset: 0;
    background:
      linear-gradient(180deg, #3f6a22 0%, #5f8f2a 22%, #8cc12b 38%, var(--grass-bright) 50%, var(--grass-mid) 100%);
  }
  .awning-photo {
    position: absolute;
    left: 179px;
    top: 49px;
    width: 972px;
    height: 464px;
    background:
      linear-gradient(90deg, #8fae6a 0%, #b0874e 30%, #a8784a 48%, #b9d08a 70%, #e4e7e4 82%, #d9dcdc 100%);
    border-radius: 6px;
  }
  .curves {
    position: absolute;
    inset: 0;
  }
  .curve-accent { fill: var(--accent-yellow); }
  .curve-band { fill: var(--brand-green); }
  .curve-corner { fill: var(--paper); }

  .headline {
    position: absolute;
    left: 461px;
    top: 597px;
    margin: 0;
    font-weight: 400;
    font-size: 38px;
    line-height: 47px;
    letter-spacing: 0.5px;
    color: var(--ink);
    text-transform: uppercase;
  }
  .badge-new {
    position: absolute;
    left: 693px;
    top: 548px;
    margin: 0;
    font-weight: 700;
    font-size: 114px;
    line-height: 114px;
    color: var(--accent-yellow);
  }
  .tagline {
    position: absolute;
    left: 462px;
    top: 762px;
    margin: 0;
    font-weight: 400;
    font-size: 25px;
    line-height: 34px;
    color: var(--ink);
  }
  .brand {
    position: absolute;
    left: 930px;
    top: 760px;
    display: flex;
    align-items: center;
    gap: 10px;
  }
  .brand-dot {
    width: 22px;
    height: 22px;
    border-radius: 50%;
    background: var(--brand-green);
  }
  .brand-name {
    font-weight: 700;
    font-size: 30px;
    color: var(--brand-green);
    white-space: nowrap;
  }
</style>
</head>
<body>
<main class="flyer">
  <div class="scene-photo" role="img" aria-label="Foto einer grünen Wiese mit Bäumen im Hintergrund"></div>
  <div class="awning-photo" role="img" aria-label="Foto eines weißen Wohnmobils mit ausgefahrener Markise und bedrucktem Sonnensegel, darauf ein Hundewelpe in einer Blumenwiese"></div>

  <svg class="curves" width="1200" height="880" viewBox="0 0 1200 880" aria-hidden="true">
    <path class="curve-accent" d="M-10,880 Q380,478 1200,458 L1200,880 Z"/>
    <path class="curve-band" d="M14,880 Q440,512 1200,489 L1200,880 Z"/>
    <path class="curve-corner" d="M810,880 Q915,606 1200,597 L1200,880 Z"/>
  </svg>

  <p class="badge-new">NEU</p>
  <h1 class="headline">Individuell<br>bedruckbare<br>Sunblocker</h1>
  <p class="tagline">Für den schönsten<br>Schatten der Welt</p>

  <div class="brand">
    <span class="brand-dot"></span>
    <span class="brand-name">Zeltholm Gear</span>
  </div>
</main>
</body>
</html>
```